Brightmill Data Works

Our company is about IT hardwares and IT solutions. IT hardware such as PC, RAMS, storage and servers. IT solutions such as project management, BA. We are also selling new technology too.

Target Market(s)

Consumer, Small to Medium Business, Corporate

Requirements
Must have
• The business card must have the following:
• Name:
• Title:
• Contact Number:
• Email address:
• Website:
• Color: Must match the logo color upgrade

```html
<!DOCTYPE html>
<html lang="en">
<head>
<meta charset="utf-8">
<title>Brightmill Data Works — Business Card</title>
<link rel="stylesheet" href="https://fonts.googleapis.com/css2?family=Montserrat:wght@400;500;700&display=swap">
<style>
  :root {
    --backdrop: #a9b9c3;
    --card-dark: #2a2a2a;
    --card-light: #eeeeec;
    --accent: #d98a2b;
    --ink: #2b2b2b;
    --ink-soft: #4a4a4a;
    --paper-white: #ffffff;
    --emboss: #dcdcd9;
  }
  * { box-sizing: border-box; margin: 0; padding: 0; }
  html, body { width: 1200px; height: 1044px; overflow: hidden; }
  body {
    background: var(--backdrop);
    font-family: "Montserrat", sans-serif;
    position: relative;
  }
  .card {
    position: absolute;
    top: 373px;
    width: 520px;
    height: 297px;
    border-bottom: 3px solid var(--accent);
    overflow: hidden;
  }
  .card--front { left: 60px; background: var(--card-dark); }
  .card--back { left: 620px; background: var(--card-light); }

  .brand {
    position: absolute;
    left: 0; right: 0; top: 50%;
    transform: translateY(-50%);
    display: flex;
    align-items: center;
    justify-content: center;
    gap: 14px;
  }
  .brand__square { width: 22px; height: 22px; background: var(--accent); }
  .brand__name {
    color: var(--paper-white);
    font-weight: 700;
    font-size: 24px;
    letter-spacing: 0.04em;
    text-transform: uppercase;
  }

  .person { position: absolute; left: 44px; top: 78px; color: var(--ink); }
  .person__name { font-weight: 700; font-size: 17px; }
  .person__title { font-weight: 400; font-size: 12px; color: var(--ink-soft); margin-top: 2px; }
  .person__web { font-size: 11px; margin-top: 16px; color: var(--ink-soft); }
  .person__web strong { font-weight: 700; color: var(--ink); }

  .contacts { position: absolute; left: 200px; top: 170px; font-size: 11px; color: var(--ink); line-height: 1.35; }
  .contacts__label { font-weight: 400; color: var(--ink-soft); }
  .contacts__value { font-weight: 500; margin-bottom: 10px; }

  .emboss-mark {
    position: absolute;
    right: 58px; bottom: 62px;
    width: 60px; height: 60px;
    border: 2px solid var(--emboss);
    box-shadow: 1px 1px 0 #ffffff;
  }
</style>
</head>
<body>
  <section class="card card--front" aria-label="Card front">
    <div class="brand">
      <span class="brand__square"></span>
      <span class="brand__name">Brightmill Data Works</span>
    </div>
  </section>

  <section class="card card--back" aria-label="Card back">
    <div class="person">
      <p class="person__name">Daniel Reyes</p>
      <p class="person__title">Managing Director</p>
      <p class="person__web">www.<strong>brightmilldata</strong>.com</p>
    </div>
    <div class="contacts">
      <p class="contacts__label">mobile</p>
      <p class="contacts__value">555.014.2280</p>
      <p class="contacts__label">email</p>
      <p class="contacts__value">hello@brightmilldata.com</p>
    </div>
    <div class="emboss-mark"></div>
  </section>
</body>
</html>
```